Velvet Dice Night Age Verification Landing Page

To create a visually appealing design for the landing page of the adult game "Velvet Dice Night" that confirms the visitor's age.
The design should have a simple and visually appealing look that focuses on two buttons labeled "Yes" and "No". The purpose of the page is to confirm that the visitor is 18 years of age or older before accessing the game's content. Responsive design that works well on desktop and mobile devices. The final output should be delivered in PSD, AI, or Sketch format, along with any necessary images or assets.
I have also attached examples.

```html
<!DOCTYPE html>
<html lang="en">
<head>
<meta charset="utf-8">
<title>Velvet Dice Night – Age Verification</title>
<link href="https://fonts.googleapis.com/css2?family=Great+Vibes&family=Montserrat:wght@400;600&display=swap" rel="stylesheet">
<style>
:root{
  --ink:#ffffff;
  --muted:#c9c2d0;
  --dark-bg:#1f2027;
  --dark-modal:rgba(18,18,22,.88);
  --plum-bg:#2a1230;
  --plum-deep:#1e0c24;
  --violet:#6a3b8e;
  --violet-light:#9a6cc0;
  --btn:#7b4d93;
  --sky:#3c9fd6;
  --handle:#c7c7c7;
}
*{box-sizing:border-box;margin:0;padding:0}
html,body{width:870px;height:1200px;overflow:hidden;background:var(--plum-deep)}
body{font-family:"Montserrat",sans-serif;color:var(--ink);position:relative}
.section{position:absolute;left:0;width:870px;overflow:hidden}
.desktop-dark{top:0;height:432px;background:var(--dark-bg)}
.desktop-plum{top:432px;height:446px;background:linear-gradient(180deg,var(--plum-bg),#331a3c)}
.mobile-row{top:878px;height:322px;background:var(--plum-deep)}
.photo{position:absolute;background:radial-gradient(ellipse at 42% 40%,#8a6d62 0%,#4a3b3c 30%,#2a2a31 62%,#1d1e24 100%)}
.photo.tinted{background:radial-gradient(ellipse at 42% 45%,#7d5a66 0%,#4a2c4e 35%,#2c1634 70%,#21102a 100%)}
.music{position:absolute;right:14px;top:14px;width:26px;height:26px;border-radius:4px;background:rgba(255,255,255,.08);display:flex;align-items:center;justify-content:center}
.brand{font-family:"Great Vibes",cursive;color:var(--ink);display:flex;align-items:center;gap:6px;line-height:1}
.brand .dot{width:8px;height:8px;border-radius:50%;background:var(--ink)}
.modal{position:absolute;text-align:center;display:flex;flex-direction:column;align-items:center;justify-content:center}
.modal-dark{left:261px;top:122px;width:348px;height:180px;background:var(--dark-modal);border:1px solid #3a3a42}
.handle{position:absolute;width:5px;height:5px;background:var(--handle)}
.question{font-size:10px;color:var(--muted);margin:10px 0 12px}
.buttons{display:flex;gap:10px}
.btn{width:46px;height:18px;background:var(--btn);color:var(--ink);font-size:8px;font-weight:600;display:flex;align-items:center;justify-content:center;letter-spacing:.5px}
.remember{display:flex;align-items:center;gap:5px;font-size:7px;color:var(--muted);margin-top:12px}
.remember i{width:7px;height:7px;border:1px solid var(--muted);display:block}
.tail{position:absolute}
.modal-violet{left:261px;top:133px;width:348px;height:180px;background:var(--violet);border:2px solid var(--violet-light);box-shadow:0 0 0 6px rgba(106,59,142,.35)}
.modal-violet .inner{position:absolute;inset:8px;border:1px solid rgba(255,255,255,.35)}
.headline{font-family:"Great Vibes",cursive;font-size:40px;line-height:1;color:var(--ink)}
.modal-violet .question{color:#ece3f4}
.modal-violet .btn{background:#fff;color:var(--violet)}
.phone{position:absolute;top:8px;height:282px;overflow:hidden;border:1px solid #3b2444}
.phone-a{left:44px;width:232px;background:var(--dark-bg)}
.phone-b{left:290px;width:262px;background:var(--plum-bg)}
.mini-modal{position:absolute;text-align:center;display:flex;flex-direction:column;align-items:center;justify-content:center}
.mini-modal .q{font-size:6px;color:var(--muted);margin:5px 0 6px}
.mini-modal .btn{width:26px;height:10px;font-size:5px}
.mini-modal .r{font-size:5px;color:var(--muted);margin-top:5px}
.big-brand{position:absolute;left:620px;top:92px;width:190px;flex-direction:column;gap:10px;font-size:40px;text-align:center}
.big-brand .dot{width:16px;height:16px}
</style>
</head>
<body>

<section class="section desktop-dark">
  <div class="photo" style="left:0;top:0;width:870px;height:432px" role="img" aria-label="Dimmed photo of a smiling woman in a black leather jacket"></div>
  <div class="music"><svg width="14" height="14" viewBox="0 0 14 14"><path d="M5 2v7.2A2 2 0 1 0 6 11V5l5-1.2v4.4A2 2 0 1 0 12 10V1z" fill="#ddd"/></svg></div>
  <div class="modal modal-dark">
    <span class="handle" style="left:-3px;top:-3px"></span><span class="handle" style="right:-3px;top:-3px"></span>
    <span class="handle" style="left:-3px;bottom:-3px"></span><span class="handle" style="right:-3px;bottom:-3px"></span>
    <div class="brand" style="font-size:20px"><span class="dot"></span>Velvet Dice Night</div>
    <p class="question">Are you over 18 Years of age?</p>
    <div class="buttons"><span class="btn">YES</span><span class="btn">NO</span></div>
    <p class="remember"><i></i>Remember my choice</p>
  </div>
</section>

<section class="section desktop-plum">
  <div class="photo tinted" style="left:120px;top:0;width:750px;height:446px" role="img" aria-label="Photo of a smiling woman in a black leather jacket, faded into purple"></div>
  <div class="brand" style="position:absolute;left:40px;top:40px;font-size:22px"><span class="dot"></span>Velvet Dice Night</div>
  <svg class="tail" style="left:440px;top:245px" width="155" height="110" viewBox="0 0 155 110">
    <path d="M0 0H150V75H120L98 105V75H0Z" fill="var(--sky)"/>
  </svg>
  <div class="modal modal-violet">
    <div class="inner"></div>
    <div class="headline">Midnight Games</div>
    <p class="question">Are you over 18 Years of age?</p>
    <div class="buttons"><span class="btn">YES</span><span class="btn">NO</span></div>
    <p class="remember" style="color:#ece3f4"><i style="border-color:#ece3f4"></i>Remember my choice</p>
  </div>
</section>

<section class="section mobile-row">
  <div class="phone phone-a">
    <div class="photo" style="inset:0" role="img" aria-label="Mobile view of the woman photo"></div>
    <div class="mini-modal" style="left:14px;top:120px;width:204px;height:90px;background:var(--dark-modal);border:1px solid #3a3a42">
      <div class="brand" style="font-size:12px"><span class="dot" style="width:5px;height:5px"></span>Velvet Dice Night</div>
      <p class="q">Are you over 18 Years of age?</p>
      <div class="buttons" style="gap:6px"><span class="btn">YES</span><span class="btn">NO</span></div>
      <p class="r">Remember my choice</p>
    </div>
  </div>
  <div class="phone phone-b">
    <div class="photo tinted" style="inset:0" role="img" aria-label="Mobile view of the woman photo in purple"></div>
    <div class="brand" style="position:absolute;left:50%;transform:translateX(-50%);top:12px;font-size:12px"><span class="dot" style="width:5px;height:5px"></span>Velvet Dice Night</div>
    <svg class="tail" style="left:120px;top:210px" width="130" height="70" viewBox="0 0 130 70"><path d="M0 0H128V46H106L88 68V46H0Z" fill="var(--sky)"/></svg>
    <div class="mini-modal" style="left:30px;top:150px;width:202px;height:96px;background:var(--violet);border:2px solid var(--violet-light)">
      <div class="headline" style="font-size:22px">Midnight Games</div>
      <p class="q" style="color:#ece3f4">Are you over 18 Years of age?</p>
      <div class="buttons" style="gap:6px"><span class="btn" style="background:#fff;color:var(--violet)">YES</span><span class="btn" style="background:#fff;color:var(--violet)">NO</span></div>
      <p class="r" style="color:#ece3f4">Remember my choice</p>
    </div>
  </div>
  <div class="brand big-brand"><span class="dot"></span>Velvet Dice Night</div>
</section>

</body>
</html>
```